NexaBRIDGE new era @ Hyper Digitalization

We need a Brochure that show all our product, services and consulting related to Hyper Digitalization into the industrial internet of things world.
We need a document that can be handled as a electronic brochure, this means that we need to show strong corporate presence, with strong skill of technology, and we have credentials and key sucess projects related to Manufacturing industries.
Key industries that we attend: Automotive, Chemical, Food and Beverage, Mining, Paper and Pulp, Oil and Gas, Energy Management.
We save money to our customer in 6 ways: 1) Eficiency in operation 2) Production Control 3) Hyper Digitalization of Thing Optimizing asset ussage 4) Maintenance and predictive of assets risks 5) Quality Control reducing Cost 6) Augmented Reality in operation and control
Target Market(s)
Manufacturing Industry. CEO of companies that has challenges of saving operation costs into plants of manufacturing.
Industry/Entity Type
Software
Other font styles liked:
- MONTSERRAT
Requirements
Must have
- Technology Enviroment, our logo, our expertise, simple message about what our company does and the DNA, infography of the company, cases of sucess, cases of savings $ using our tecnology and services, what we can do for the customer in a few words
Nice to have
- standarize our colors related to our presentation, futuristic, information related to Artificial Inteligence related to machinery
Should not have
- old version of technology,

```html
<!DOCTYPE html>
<html lang="en">
<head>
<meta charset="utf-8">
<title>NexaBRIDGE Brochure 2021</title>
<link href="https://fonts.googleapis.com/css2?family=Montserrat:wght@400;500;600;700;800&display=swap" rel="stylesheet">
<style>
:root{
  --bg:#b4b2b3;
  --blue:#1f5aa6;
  --navy:#1a3d70;
  --mid:#2a6bb5;
  --sky:#3d8fd8;
  --paper:#f2f2f3;
  --ink:#2a2f38;
  --white:#ffffff;
}
*{margin:0;padding:0;box-sizing:border-box}
html,body{width:1023px;height:1200px;overflow:hidden;background:var(--bg);font-family:'Montserrat',sans-serif;color:var(--ink)}
.canvas{position:relative;width:1023px;height:1200px}
.sheet{position:absolute;background:var(--paper);overflow:hidden;box-shadow:0 2px 6px rgba(0,0,0,.18)}
.abs{position:absolute}
.brand{font-family:'Montserrat',sans-serif;font-weight:500;letter-spacing:.5px;white-space:nowrap}

/* cover */
.cover{left:253px;top:42px;width:524px;height:376px;background:var(--white)}
.cover__band{left:0;top:0;width:524px;height:70px;background:var(--blue)}
.cover__band .brand{position:absolute;left:0;right:0;top:18px;text-align:center;color:var(--white);font-size:28px}
.cover__photo{left:0;top:70px;width:524px;height:233px;background:linear-gradient(180deg,#6c7079 0%,#8f939a 45%,#a7aab0 100%)}
.cover__title{left:0;right:0;top:150px;text-align:center;color:var(--white);font-weight:800;font-size:24px}
.cover__rule{left:145px;top:188px;width:234px;height:1px;background:rgba(255,255,255,.8)}
.cover__rule-bold{left:223px;top:186px;width:78px;height:4px;background:var(--white)}
.cover__foot{left:0;top:303px;width:524px;height:73px;background:linear-gradient(180deg,#fff,#ececee)}
.badge{position:absolute;width:84px;height:84px;border-radius:50%;border:5px solid var(--blue);background:var(--white);top:257px;display:flex;align-items:center;justify-content:center}
.badge__art{width:56px;height:56px;border-radius:50%;background:linear-gradient(135deg,#dfe7f2,#b9c9de)}
.badge .brand{font-size:15px;color:var(--ink)}
.badge-label{position:absolute;top:348px;width:170px;text-align:center;font-size:8.5px;font-weight:700;color:var(--ink)}

/* spreads */
.spread{left:54px;width:921px;height:331px}
.spread--one{top:468px}
.spread--two{top:834px}
.page{position:absolute;top:0;height:331px}
.page--left{left:0;width:457px}
.page--right{left:457px;width:464px;background:linear-gradient(90deg,#e9e9eb,#f6f6f7)}
.seam{position:absolute;left:456px;top:0;width:2px;height:331px;background:linear-gradient(90deg,rgba(0,0,0,.12),rgba(0,0,0,0))}

.heading{position:absolute;font-weight:800;font-size:16px;color:var(--blue);white-space:nowrap}
.vline{position:absolute;width:1.5px;background:var(--blue)}
.body{position:absolute;font-size:8.4px;line-height:11.5px;color:var(--ink)}
.bullets{list-style:none;position:absolute;font-size:8.4px;line-height:11.3px}
.bullets li{position:relative;padding-left:19px}
.bullets li::before{content:"";position:absolute;left:2px;top:2px;width:5px;height:5px;border:1.8px solid var(--blue);border-radius:50%}
.footline{position:absolute;height:1px;background:var(--blue)}
.pageno{position:absolute;width:13px;height:13px;border:1px solid var(--blue);border-radius:50%;font-size:6px;font-weight:700;color:var(--navy);display:flex;align-items:center;justify-content:center;background:var(--white)}

/* spread one */
.field-photo{left:0;top:0;width:228px;height:331px;background:linear-gradient(180deg,#4a6f98 0%,#5b7ea6 40%,#3e5f87 70%,#5a7898 100%)}
.objective-title{left:112px;top:24px;font-size:14.5px}
.objective-title .on-photo{color:var(--white)}
.objective-box{left:218px;top:52px;width:239px;height:53px;background:var(--blue);padding:6px 10px 0 32px;color:var(--white);font-weight:700;font-size:8.4px;line-height:11px}
.field-brand{left:34px;top:283px;color:var(--white);font-size:22px}
.desk-photo{left:270px;top:0;width:194px;height:270px;background:radial-gradient(ellipse at 70% 40%,#d7d7d9 0%,#e6e6e8 45%,rgba(240,240,241,0) 75%)}
.themes-brand{right:16px;top:14px;color:var(--white);font-size:13px}
.benefits-band{left:0;top:167px;width:205px;height:21px;background:var(--blue);border-radius:0 11px 11px 0;box-shadow:4px 0 0 var(--sky)}
.benefits-band span{position:absolute;left:31px;top:1px;color:var(--white);font-weight:800;font-size:16px;white-space:nowrap}

/* spread two */
.dna-top{left:0;top:0;width:457px;height:86px;background:var(--paper)}
.drive-photo{left:0;top:86px;width:457px;height:245px;background:linear-gradient(160deg,#264b7e 0%,#1d4276 50%,#234a80 100%)}
.brand--blue{color:var(--blue);font-size:14px}
.commit-title{left:0;right:0;top:158px;text-align:center;color:var(--white);font-weight:800;font-size:16px}
.commit-rule{left:171px;top:183px;width:117px;height:1px;background:rgba(255,255,255,.7)}
.commit-rule-bold{left:214px;top:182px;width:33px;height:3px;background:var(--white)}
.commit-list{position:absolute;left:30px;right:30px;top:194px;text-align:center;color:var(--white);font-size:8.4px;line-height:11.5px;list-style:none}
.commit-list li{margin-bottom:5px}
.commit-list li::before{content:"";display:inline-block;width:4px;height:4px;border:1.6px solid var(--white);border-radius:50%;margin-right:6px;vertical-align:1px}
.strategy-band{left:0;top:140px;width:464px;height:133px;background:linear-gradient(180deg,#e3e6ea,#edeef0)}
.step-label{position:absolute;font-size:7.2px;font-weight:700;color:var(--ink);white-space:nowrap;transform:translateX(-50%)}
</style>
</head>
<body>
<div class="canvas">

  <!-- cover -->
  <section class="sheet cover">
    <div class="abs cover__band"><span class="brand">NexaBRIDGE</span></div>
    <div class="abs cover__photo" role="img" aria-label="Photograph of an automated bottling line in an industrial plant"></div>
    <h1 class="abs cover__title">BROCHURE NEXABRIDGE 2021</h1>
    <div class="abs cover__rule"></div>
    <div class="abs cover__rule-bold"></div>
    <div class="abs cover__foot"></div>
    <div class="badge" style="left:56px"><div class="badge__art" role="img" aria-label="Industrial automation icon"></div></div>
    <div class="badge" style="left:226px"><div class="badge__art" role="img" aria-label="Industry 4.0 factory icon"></div></div>
    <div class="badge" style="left:396px"><span class="brand">VALTRIX</span></div>
    <div class="badge-label" style="left:13px">INDUSTRIAL AUTOMATION</div>
    <div class="badge-label" style="left:183px">INDUSTRY 4.0</div>
    <div class="badge-label" style="left:353px">VALTRIX SOLUTIONS</div>
  </section>

  <!-- spread one -->
  <section class="sheet spread spread--one">
    <div class="page page--left" style="background:var(--paper)">
      <div class="abs field-photo" role="img" aria-label="Photograph of a combine harvester in a wheat field under a blue tint"></div>
      <div class="abs brand field-brand">NexaBRIDGE</div>
      <h2 class="heading objective-title"><span class="on-photo">OBJECTIVE OF </span>BROCHURE / KEY MESSAGES</h2>
      <div class="abs objective-box">Brochure to be delivered by our marketing process and sales, This brochure will be deliverted to CEO´s worldwide in Industrial companies.</div>
      <p class="body" style="left:250px;top:113px;width:200px">Need to show in a few pages, what we can do for them:</p>
      <ul class="bullets" style="left:254px;top:140px;width:196px">
        <li style="margin-bottom:11px">We offer product and projects to transform operations in manufacturing.</li>
        <li style="margin-bottom:11px">Our work drives customers to Competitive Advantage Mode.</li>
        <li style="margin-bottom:11px">We use Artificial Intelligence, Hyper Digitalization and Machine Learning techniques to obtain cost reduction in Production Process, Better Quality Delivery, Asset &amp; Optimization Performance.</li>
        <li>We add productivity without changes into their actual operations in assetts</li>
      </ul>
      <div class="footline" style="left:228px;top:315px;width:208px"></div>
      <div class="pageno" style="left:436px;top:309px">01</div>
    </div>
    <div class="page page--right">
      <div class="abs desk-photo" role="img" aria-label="Photograph of a keyboard, a latte cup and a notebook on a desk"></div>
      <div class="abs brand themes-brand">NexaBRIDGE</div>
      <div class="vline" style="left:21px;top:0;height:45px"></div>
      <h2 class="heading" style="left:31px;top:22px">THEMES</h2>
      <ul class="bullets" style="left:34px;top:55px;width:210px">
        <li style="margin-bottom:11px">We offer high performance technology</li>
        <li style="margin-bottom:11px">State of the art in techniques with Artificial Intelligence and prototypes for new ways of doing manufacturing</li>
        <li>We play the rol as an Architect for a Digital world into the shopfloor operation at Machine Levels</li>
      </ul>
      <div class="abs benefits-band"><span>TERMS @ BENEFITS</span></div>
      <ul class="bullets" style="left:34px;top:200px;width:410px">
        <li style="margin-bottom:6.6px">Reduce cost operation in manufacturing in 30%</li>
        <li style="margin-bottom:6.6px">Save 17% in Energy for production</li>
        <li style="margin-bottom:6.6px">Zero Unplanned Downtime in machine level</li>
        <li style="margin-bottom:6.6px">Supply Chain optimization by 1% of the cost of goods</li>
        <li style="margin-bottom:6.6px">Optimize consistency in recipes by 10% delivers 32% of cost reduction</li>
        <li>Augmented Reality functions, adds 60% of productivity and efficiency at operator levels</li>
      </ul>
      <div class="footline" style="left:0;top:312px;width:432px"></div>
      <div class="pageno" style="left:432px;top:306px">02</div>
    </div>
    <div class="seam"></div>
  </section>

  <!-- spread two -->
  <section class="sheet spread spread--two">
    <div class="page page--left">
      <div class="abs dna-top"></div>
      <div class="vline" style="left:24px;top:0;height:45px"></div>
      <h2 class="heading" style="left:34px;top:22px">OUR DNA</h2>
      <div class="abs brand brand--blue" style="right:14px;top:23px">NexaBRIDGE</div>
      <p class="body" style="left:39px;top:50px;width:400px">We want all companies to operate in an automated way, to be more efficient and to compete with whoever is globally. We have the knowledge and experience to achieve it.</p>
      <div class="abs drive-photo" role="img" aria-label="Photograph of a hand on a car steering wheel and dashboard under a blue tint"></div>
      <h2 class="abs commit-title">OUR COMMITMENTS</h2>
      <div class="abs commit-rule"></div>
      <div class="abs commit-rule-bold"></div>
      <ul class="commit-list">
        <li>Improve the operation of each company individually.</li>
        <li>Impact the country's competitiveness.</li>
        <li>Support companies to access the highest levels of development, productivity, financing and profitability.</li>
      </ul>
      <div class="footline" style="left:0;top:317px;width:436px;background:rgba(255,255,255,.7)"></div>
      <div class="pageno" style="left:436px;top:311px">03</div>
    </div>
    <div class="page page--right">
      <div class="vline" style="left:21px;top:0;height:45px"></div>
      <h2 class="heading" style="left:31px;top:21px">CONSULTING STRATEGY</h2>
      <div class="abs brand brand--blue" style="right:14px;top:23px">NexaBRIDGE</div>
      <p class="body" style="left:36px;top:50px;width:400px">We know that all customers are in different maturity level of digitalization.</p>
      <p class="body" style="left:36px;top:67px;width:400px">Our Strategy helps to start simple, low cost and produce big changes</p>
      <p class="body" style="left:36px;top:84px;width:400px">We have a graphic that represents the levels, and we need to show into a graph that we can help them to take positive path of optimization</p>
      <div class="abs strategy-band"></div>
      <svg class="abs" style="left:0;top:140px" width="464" height="133" viewBox="0 0 464 133" aria-label="Six step maturity path">
        <g fill="none" stroke="var(--blue)" stroke-width="3" stroke-linecap="round" stroke-linejoin="round">
          <path d="M92 33 A30 30 0 1 0 71 84 M71 84 V100 M65 94 L71 100 L77 94"/>
          <path d="M108 89 A30 30 0 1 0 129 38 M129 38 V12 M123 18 L129 12 L135 18" stroke="var(--navy)"/>
          <path d="M211 33 A30 30 0 1 0 190 84 M190 84 V100 M184 94 L190 100 L196 94"/>
          <path d="M233 89 A30 30 0 1 0 254 38 M254 38 V12 M248 18 L254 12 L260 18" stroke="var(--navy)"/>
          <path d="M338 33 A30 30 0 1 0 317 84 M317 84 V100 M311 94 L317 100 L323 94"/>
          <path d="M361 89 A30 30 0 1 0 382 38 M382 38 V12 M376 18 L382 12 L388 18" stroke="var(--navy)"/>
        </g>
        <g font-family="Montserrat, sans-serif" font-weight="800" font-size="13" fill="#fff" text-anchor="middle">
          <circle cx="71" cy="54" r="22" fill="var(--mid)"/><text x="71" y="59">01</text>
          <circle cx="129" cy="68" r="22" fill="var(--navy)"/><text x="129" y="73">02</text>
          <circle cx="190" cy="54" r="22" fill="var(--mid)"/><text x="190" y="59">03</text>
          <circle cx="254" cy="68" r="22" fill="var(--navy)"/><text x="254" y="73">04</text>
          <circle cx="317" cy="54" r="22" fill="var(--mid)"/><text x="317" y="59">05</text>
          <circle cx="382" cy="68" r="22" fill="var(--navy)"/><text x="382" y="73">06</text>
        </g>
      </svg>
      <span class="step-label" style="left:129px;top:143px">INTERCONNECTED</span>
      <span class="step-label" style="left:254px;top:143px">AUTOMATED</span>
      <span class="step-label" style="left:382px;top:143px">MANUAL OPERATIONS</span>
      <span class="step-label" style="left:71px;top:254px">INDUSTRY 4.0 IIOT</span>
      <span class="step-label" style="left:190px;top:254px">STORAGING</span>
      <span class="step-label" style="left:317px;top:254px">INSTRUMENTED</span>
      <div class="footline" style="left:0;top:312px;width:432px"></div>
      <div class="pageno" style="left:432px;top:306px">04</div>
    </div>
    <div class="seam"></div>
  </section>

</div>
</body>
</html>
```